Wandering Rooms Stationary Set

Wandering Rooms is a bespoke interior design firm set to provide services to VIP clients with elegance and minimalism is the main theme for our stationary set. We require a full stationary set covering A4 letterhead, A4 & A3 envelopes, business cards, USB's, CDs, email signature and any other item the designer sees fit. logo is already designed and finalized, and we require the designer to use it as is without modifying the logo.

Address to be used on letterhead / business cards ...etc shall be as follows:

Phone : +971 2 518 2047
P.O. Box : 309186
Address: Block C&D, Bldg. 47, Court 12, Abu Dhabi, United Arab Emirates
Website: www.wanderingrooms-example.com

Target Market(s)

VIP Clients

Industry/Entity Type

Interior Design

Font styles to use
Other font styles liked:
• something to be unique

Colors

Designer to choose colors to be used in the design.

Requirements
Must have
• Elegant, minimalistic
Nice to have
• Simple yet elegant design having a sharp yet clean cut format
Should not have
• No additional colours, just colours that are used in the logo (silver, black or gold)

```html
<!DOCTYPE html>
<html lang="en">
<head>
<meta charset="utf-8">
<title>Wandering Rooms – Business Card</title>
<link rel="stylesheet" href="https://fonts.googleapis.com/css2?family=Montserrat:wght@400;500;700&display=swap">
<style>
  :root {
    --bg: #dcdcdb;
    --ink: #1f1c1c;
    --paper: #fbfbfa;
    --gold: #b8924a;
    --silver: #c9c9c9;
    --white: #ffffff;
  }
  * { margin: 0; padding: 0; box-sizing: border-box; }
  html, body { width: 1200px; height: 810px; overflow: hidden; }
  body {
    background: var(--bg);
    font-family: "Montserrat", sans-serif;
    position: relative;
  }
  .card {
    position: absolute;
    top: 250px;
    width: 540px;
    height: 310px;
    overflow: hidden;
    box-shadow: 0 6px 18px rgba(0,0,0,0.18);
  }
  .card--contact { left: 40px; background: var(--paper); }
  .card--brand { left: 620px; background: var(--ink); }

  .card__shape { position: absolute; inset: 0; }

  .brand-name {
    font-family: "Montserrat", sans-serif;
    font-weight: 500;
    color: var(--gold);
    text-transform: uppercase;
    letter-spacing: 0.22em;
    white-space: nowrap;
  }
  .card--contact .brand-name {
    position: absolute;
    left: 28px;
    top: 178px;
    font-size: 13px;
  }
  .card--brand .brand-name {
    position: absolute;
    left: 0; right: 0;
    top: 118px;
    text-align: center;
    font-size: 26px;
  }

  .contact {
    position: absolute;
    left: 338px;
    top: 44px;
    color: var(--white);
    font-size: 9px;
    line-height: 1.45;
  }
  .contact__name { color: var(--gold); font-weight: 700; font-size: 15px; line-height: 1.1; }
  .contact__role { font-size: 10px; margin-bottom: 12px; }
  .contact__address { margin-bottom: 12px; }
  .contact__list { list-style: none; }
  .contact__list li { display: flex; align-items: center; gap: 6px; }
  .contact__icon { width: 8px; height: 8px; flex: none; }

  .web {
    position: absolute;
    left: 0; right: 0;
    bottom: 54px;
    text-align: center;
    font-size: 13px;
    font-weight: 500;
    color: var(--white);
  }
  .web__domain { color: var(--gold); }
</style>
</head>
<body>

  <section class="card card--contact">
    <svg class="card__shape" viewBox="0 0 540 310" aria-hidden="true">
      <path d="M215 0 C245 85 300 110 312 175 C322 240 332 280 345 310 L540 310 L540 0 Z" fill="var(--ink)"/>
      <path d="M219 0 C249 85 304 110 316 175 C326 240 336 280 349 310" fill="none" stroke="var(--gold)" stroke-width="2.5"/>
      <path d="M210 0 C240 87 294 112 306 177 C316 242 326 282 339 310" fill="none" stroke="var(--silver)" stroke-width="1.5" opacity="0.6"/>
    </svg>

    <div class="brand-name">Wandering Rooms</div>

    <div class="contact">
      <p class="contact__name">Karim Haddad</p>
      <p class="contact__role">Managing Director</p>
      <p class="contact__address">P.O. Box : 309186<br>Block C&amp;D, Bldg. 47, Court 12<br>Abu Dhabi, United Arab Emirates</p>
      <ul class="contact__list">
        <li>
          <svg class="contact__icon" viewBox="0 0 10 10" aria-hidden="true"><path d="M2 1 L4 1 L4.6 3 L3.4 3.8 C4 5.2 4.8 6 6.2 6.6 L7 5.4 L9 6 L9 8 C5 9 1 5 2 1 Z" fill="var(--gold)"/></svg>
          +971 2 518 2047
        </li>
        <li>
          <svg class="contact__icon" viewBox="0 0 10 10" aria-hidden="true"><rect x="0.8" y="2" width="8.4" height="6" fill="none" stroke="var(--gold)"/><path d="M0.8 2 L5 5.5 L9.2 2" fill="none" stroke="var(--gold)"/></svg>
          info@wanderingrooms-example.com
        </li>
        <li>
          <svg class="contact__icon" viewBox="0 0 10 10" aria-hidden="true"><circle cx="5" cy="5" r="4.5" fill="var(--gold)"/></svg>
          www.wanderingrooms-example.com
        </li>
      </ul>
    </div>
  </section>

  <section class="card card--brand">
    <div class="brand-name">Wandering Rooms</div>
    <p class="web">www.<span class="web__domain">wanderingrooms-example</span>.com</p>
  </section>

</body>
</html>
```